Packaging and labelling for Swiss made Organic CBD Oil

Visit our website www.clearleafmerida.example
We have not put any product on yet as require packaging and label design .
Website will give you a great feel for the company and how we have used
the logo . The Vextora cbd product shown is a company similar to ourselves with similar core values , we liked the clean packaging design they have .

Im happy if you want use the mandala symbol in our logo separate from
KELVORA, to separate and use the mandala symbol as a larger icon than
it appears in our logo
Clean , Pure , organic feel. Like the product to look pharmaceutical and life changing not gimmicky.
Colours to go with or be the same as our logo colours
But not too cold and clinical
Bottle size 84mm x 25mm
Label size 75mm x 30mm
Box 30mm x 30mm x 100mm
6 products
Full Spectrum :
500mg CBD (5%)
1000mg CBD ( 10% )
1500mg CBD (15%)
2000mg CBD ( 20% )
Broad spectrum THC Free
500mg CBD (5%)
Pets
500mg Broad Spectrum THC Free
Updates

Would like the design to be more modern than traditional

LABEL Information Front of Bottle - Logo KELVORA & Mandala - Mandala can be used separately as design symbol Organic Cannabis Oil 1500mg CBD (15%) Ful Spectrum 10ml Back of bottle Ingredients: Organic Cannabis Oil Extract Organic Sunflower Seed Oil THC - 0.2% Certified Swiss Organic Cultivation Shake well before use. Store in a cool , dry place and out of the each of children BOX information Front and rear Logo - KELVORA & Mandala - Mandala can be used separately as a design symbol Organic Cannabis Oil 1500mg CBD (15%) Full Spectrum Sides x 2 This product is a food supplement and is not intended to diagnose, treat, cure or prevent any disease If you are pregnant, lactating or taking any medication consult your health care practitioner Suitable for vegetarians and vegans Ingredients Organic Cannabis Oil extract Organis Sunflower Oil Store in a cool ,dry place, out of the reach of children Recommended Use 1-5 drops ( 1 drop = 7.5mg CBD ) Subject to body weight and personal requirement - visit www.clearleafmerida for more information 100% Natural 100% Organic GMO free 100% Vegan ( symbol with each ) Expiry date see bottle label Cultivated and manufactured in Switzerland

Target Market(s)

age 40 - 80

Font styles to use
Other font styles liked:
• In our website we have used Open Sans for the copy and Lato for headings .

Requirements
Must have
• look like an Industry leader
Kelvora will change the quality of peoples lives and in some cases may
even save lives so want look powerful and credible
Our Mission is - Through Delivering Pure , Premium , Organic products we will educate, inform and help people achieve healthier , happier lifestyles
Nice to have
• Colours to look good with our logo colours or be the same as our logo
colours
Logo Font - Avenir Black and Avenir Book

Font used in website - Content - Open Sans / Headings - Lato
If you have another font for the packaging information that will go well with
our logo, I'm happy for you to use your skills

```html
<!DOCTYPE html>
<html lang="en">
<head>
<meta charset="utf-8">
<title>Kelvora – CBD Oil Label</title>
<link rel="stylesheet" href="https://fonts.googleapis.com/css2?family=Nunito+Sans:wght@300;400;800;900&family=Montserrat:wght@800&display=swap">
<style>
  :root {
    --page: #ffffff;
    --label-edge: #c9c9c9;
    --ink: #2f2f2f;
    --ink-soft: #6b6b6b;
    --organic-green: #6ab84f;
    --swiss-red: #e2231a;
    --aqua: #9fd8d8;
    --aqua-mark: #8fd0d0;
  }
  * { margin: 0; padding: 0; box-sizing: border-box; }
  html, body {
    width: 1200px;
    height: 1000px;
    overflow: hidden;
    background: var(--page);
  }
  .canvas {
    position: relative;
    width: 1200px;
    height: 1000px;
    background: var(--page);
  }
  .bottle-label {
    position: absolute;
    left: 100px;
    top: 159px;
    width: 1000px;
    height: 682px;
    border: 1px solid var(--label-edge);
    background: #fff;
    overflow: hidden;
    font-family: "Nunito Sans", "Avenir", sans-serif;
    color: var(--ink);
  }
  .label-column {
    position: absolute;
    left: 353px;
    width: 294px;
  }
  .brand {
    top: 52px;
    display: flex;
    align-items: center;
    gap: 10px;
  }
  .brand-dot {
    width: 14px;
    height: 14px;
    border-radius: 50%;
    background: var(--aqua-mark);
    flex: none;
    margin-top: -30px;
  }
  .brand-name {
    font-weight: 900;
    font-size: 64px;
    letter-spacing: 5px;
    line-height: 1;
    color: var(--ink);
  }
  .claim-row {
    top: 224px;
    height: 39px;
    display: flex;
    align-items: center;
    gap: 6px;
  }
  .organic-tag {
    background: var(--organic-green);
    color: #fff;
    font-weight: 800;
    font-size: 36px;
    line-height: 39px;
    height: 39px;
    padding: 0 5px;
    letter-spacing: 0.5px;
  }
  .swiss-square {
    width: 38px;
    height: 39px;
    background: var(--swiss-red);
    flex: none;
  }
  .swiss-made {
    font-family: "Nunito Sans", sans-serif;
    font-weight: 800;
    font-size: 17px;
    line-height: 18px;
    color: var(--ink);
    transform: scaleX(0.78);
    transform-origin: left center;
  }
  .product-name {
    top: 266px;
    font-weight: 800;
    font-size: 75px;
    line-height: 1;
    letter-spacing: -2px;
    color: var(--ink);
  }
  .thc-free {
    top: 341px;
    font-family: "Montserrat", sans-serif;
    font-weight: 800;
    font-size: 42px;
    line-height: 1;
    letter-spacing: 10px;
    color: var(--ink);
    white-space: nowrap;
  }
  .strength {
    top: 440px;
    width: 320px;
    left: 348px;
    text-align: center;
    font-weight: 300;
    font-size: 66px;
    line-height: 68px;
    color: var(--ink-soft);
  }
  .volume-band {
    position: absolute;
    left: 358px;
    top: 621px;
    width: 286px;
    height: 61px;
    background: var(--aqua);
    display: flex;
    align-items: center;
    justify-content: center;
    font-weight: 900;
    font-size: 38px;
    letter-spacing: -1px;
    color: #1f1f1f;
  }
</style>
</head>
<body>
  <main class="canvas">
    <section class="bottle-label" aria-label="Kelvora CBD oil bottle label">
      <div class="label-column brand">
        <span class="brand-dot" aria-hidden="true"></span>
        <span class="brand-name">KELVORA</span>
      </div>

      <div class="label-column claim-row">
        <span class="organic-tag">ORGANIC</span>
        <span class="swiss-square" aria-hidden="true"></span>
        <span class="swiss-made">SWISS<br>MADE</span>
      </div>

      <h1 class="label-column product-name">CBD OIL</h1>
      <p class="label-column thc-free">THC FREE</p>

      <p class="label-column strength">20% CBD<br>(2000mg)</p>

      <div class="volume-band">30 ML (1OZ)</div>
    </section>
  </main>
</body>
</html>
```